German Headhunter/ HR Consultancy needs Business Cards Design

We need a business Card Design for our Company in Stuttgart. We are specialized as Headhunter/ HR Consultancy in Placement of specialist and managers in permanent employment. Please refer to our business logo.

```html
<!DOCTYPE html>
<html lang="de">
<head>
<meta charset="utf-8">
<title>Vantera Personalberatung – Business Cards</title>
<link href="https://fonts.googleapis.com/css2?family=Montserrat:wght@500;700&family=Arimo:wght@400&display=swap" rel="stylesheet">
<style>
  :root {
    --stage: #e9e9e9;
    --card-white: #ffffff;
    --card-dark: #2a2a2b;
    --pattern-dark: #333335;
    --pattern-light: #505052;
    --brand-blue: #3551a8;
    --text-grey: #8a8a8a;
    --rule-grey: #a8a8a8;
    --band-grey: #c4c6cc;
    --white: #ffffff;
  }
  * { box-sizing: border-box; margin: 0; padding: 0; }
  html, body { width: 1200px; height: 802px; overflow: hidden; }
  body {
    background: var(--stage);
    font-family: "Arimo", Arial, sans-serif;
    position: relative;
  }
  .card {
    position: absolute;
    top: 236px;
    width: 530px;
    height: 310px;
    border-radius: 2px;
    box-shadow: 0 6px 18px rgba(0,0,0,.18);
    overflow: hidden;
  }
  /* front */
  .card-front { left: 50px; background: var(--card-white); }
  .front-mark {
    position: absolute; right: 40px; top: 28px;
    width: 150px; height: 150px;
    background: var(--brand-blue);
  }
  .brand {
    position: absolute; left: 40px; top: 58px;
    display: flex; align-items: center; gap: 12px;
  }
  .brand-square { width: 34px; height: 34px; background: var(--brand-blue); flex: none; }
  .brand-name {
    font-family: "Montserrat", Arial, sans-serif;
    font-weight: 700; color: var(--brand-blue);
    font-size: 22px; letter-spacing: .5px; line-height: 1.1;
  }
  .brand-name small { display: block; font-size: 11px; letter-spacing: 1px; }
  .person { position: absolute; left: 40px; top: 128px; }
  .person-name {
    font-family: "Montserrat", Arial, sans-serif; font-weight: 700;
    color: var(--brand-blue); font-size: 17px; letter-spacing: .5px;
  }
  .person-role { color: var(--text-grey); font-size: 13px; margin-top: 2px; }
  .contacts { list-style: none; margin-top: 12px; }
  .contacts li {
    display: flex; align-items: center; gap: 8px;
    color: var(--text-grey); font-size: 13px; line-height: 20px;
  }
  .contacts svg { width: 12px; height: 12px; fill: var(--brand-blue); flex: none; }
  .address-rule {
    position: absolute; left: 40px; right: 40px; top: 250px;
    border-top: 1px solid var(--rule-grey);
  }
  .address {
    position: absolute; left: 40px; top: 258px;
    color: var(--text-grey); font-size: 13px;
  }
  .front-band {
    position: absolute; left: 0; right: 0; bottom: 0; height: 10px;
    display: flex;
  }
  .front-band .grey { width: 34px; background: var(--band-grey); }
  .front-band .blue { flex: 1; background: var(--brand-blue); }
  /* back */
  .card-back { left: 620px; background: var(--card-dark); }
  .back-pattern {
    position: absolute; inset: 0;
    background: linear-gradient(110deg, var(--pattern-dark) 40%, var(--pattern-light) 100%);
  }
  .back-brand {
    position: absolute; left: 190px; top: 128px;
    display: flex; align-items: center; gap: 12px;
  }
  .back-brand .brand-name { color: var(--white); }
</style>
</head>
<body>
  <section class="card card-front" aria-label="Business card front">
    <div class="front-mark" aria-hidden="true"></div>
    <div class="brand">
      <span class="brand-square" aria-hidden="true"></span>
      <p class="brand-name">VANTERA<small>PERSONALBERATUNG</small></p>
    </div>
    <div class="person">
      <p class="person-name">LUKAS BRENNER</p>
      <p class="person-role">Manager</p>
      <ul class="contacts">
        <li><svg viewBox="0 0 12 12"><path d="M2.5 1h2l1 2.5-1.3 1a6 6 0 0 0 3.3 3.3l1-1.3L11 7.5v2a1.5 1.5 0 0 1-1.5 1.5A8.5 8.5 0 0 1 1 2.5 1.5 1.5 0 0 1 2.5 1z"/></svg>+49 711 482 3150</li>
        <li><svg viewBox="0 0 12 12"><path d="M1 2.5h10v7H1z M1 2.5l5 4 5-4" fill="none" stroke="#3551a8" stroke-width="1.3"/></svg>l.brenner@vantera-hr.de</li>
        <li><svg viewBox="0 0 12 12"><circle cx="6" cy="6" r="5" fill="none" stroke="#3551a8" stroke-width="1.3"/><path d="M1 6h10M6 1c-2.5 3-2.5 7 0 10M6 1c2.5 3 2.5 7 0 10" fill="none" stroke="#3551a8" stroke-width="1"/></svg>www.vantera-hr.de</li>
      </ul>
    </div>
    <div class="address-rule"></div>
    <p class="address">Königstraße 48, 70173 Stuttgart</p>
    <div class="front-band"><span class="grey"></span><span class="blue"></span></div>
  </section>

  <section class="card card-back" aria-label="Business card back">
    <div class="back-pattern" role="img" aria-label="Embossed repeating brand pattern on dark card stock"></div>
    <div class="back-brand">
      <span class="brand-square" aria-hidden="true"></span>
      <p class="brand-name">VANTERA<small>PERSONALBERATUNG</small></p>
    </div>
  </section>
</body>
</html>
```